WordPress Site That Reviews Footwear

We need a wordpress web design for an affiliate site called PaceKite. We review and do roundups on footwear products. The final design should be clean and mobile friendly. The site should be built with Gutenberg page builder. We like the design of https://lunavessel.com/.
Updates

Need extra days to review

Target Market(s)

USA

Industry/Entity Type

Footwear

Logo Text

PaceKite

Number of Pages Required

4 page

Font styles to use
Serif
Sans Serif

Requirements
Must have
• Wordpress site
Blog post
Page
Categories
Homepage

```html
<!DOCTYPE html>
<html lang="en">
<head>
<meta charset="utf-8">
<title>PaceKite – Footwear Reviews</title>
<link href="https://fonts.googleapis.com/css2?family=Jost:wght@400;500&display=swap" rel="stylesheet">
<style>
:root{
  --teal:#1aae9a;
  --teal-dark:#14927f;
  --blue:#1a5a98;
  --ink:#2b2b2b;
  --text:#444;
  --muted-bg:#f5f5f5;
  --line:#cfcfcf;
  --white:#fff;
}
*{box-sizing:border-box;margin:0;padding:0}
html,body{width:1200px;height:3184px;overflow:hidden}
body{position:relative;font-family:'Jost',sans-serif;color:var(--text);background:var(--white)}
.abs{position:absolute}

/* header */
.site-header{position:absolute;left:0;top:0;width:1200px;height:161px;border-bottom:1px solid #e4e4e4;box-shadow:0 2px 6px rgba(0,0,0,.08);background:var(--white);z-index:2}
.brand{position:absolute;left:111px;top:40px;display:flex;align-items:center;gap:12px}
.brand-dot{width:44px;height:44px;border-radius:50%;background:var(--teal)}
.brand-name{font-size:34px;font-weight:500;letter-spacing:1px;color:var(--ink)}
.search{position:absolute;left:806px;top:30px;width:282px;height:47px;border:1px solid #bbb;border-radius:24px;padding:0 22px;display:flex;align-items:center;justify-content:space-between;font-size:16px;color:#555}
.main-nav{position:absolute;right:111px;top:110px;display:flex;gap:41px;font-size:18px;font-weight:500;color:var(--ink)}
.main-nav .active{color:var(--blue)}

/* hero */
.hero{position:absolute;left:0;top:161px;width:1200px;height:702px;background:linear-gradient(180deg,#9c9ea3 0%,#b4b5b8 40%,#6f7074 62%,#4a4b4f 100%)}
.hero-photo{position:absolute;left:470px;top:120px;width:620px;height:500px;border-radius:40% 50% 30% 30%;background:linear-gradient(160deg,#2a2a2e 0%,#1b1b1f 60%,#5b3cc4 85%,#c03aa8 100%);opacity:.92}
.hero-title{position:absolute;left:110px;top:120px;font-size:76px;font-weight:500;color:var(--teal);letter-spacing:-1px}
.hero-text{position:absolute;left:111px;top:225px;width:460px;font-size:18.5px;font-weight:500;line-height:37px;color:var(--ink)}
.btn{display:inline-flex;align-items:center;justify-content:center;border-radius:30px;color:var(--white);font-size:19px}
.hero-btn{position:absolute;left:112px;top:321px;width:166px;height:53px;background:linear-gradient(90deg,var(--teal),var(--blue))}
.dots{position:absolute;left:575px;top:669px;display:flex;gap:7px}
.dots span{width:12px;height:12px;border-radius:50%;background:var(--white)}
.dots span.on{background:var(--teal)}

/* section titles */
.sec-title{font-size:40px;font-weight:500;color:var(--ink);text-align:center}
.sec-title em{font-style:normal;color:var(--teal)}
.rule{width:52px;height:3px;background:var(--teal)}

.welcome-title{position:absolute;left:0;top:912px;width:1200px}
.welcome-rule{position:absolute;left:574px;top:975px}
.welcome-text{position:absolute;left:230px;top:995px;width:740px;text-align:center;font-size:14.6px;line-height:31px;color:#444}

.cards{position:absolute;left:112px;top:1159px;display:flex;gap:16px}
.card{width:233px;height:231px;border:2px solid var(--teal);border-radius:8px;text-align:center;padding-top:26px}
.card.blue{border-color:var(--blue)}
.card svg{display:block;margin:0 auto;height:84px}
.card h3{margin-top:16px;font-size:22px;font-weight:500;color:var(--teal)}
.card.blue h3{color:var(--blue)}
.card p{margin:6px auto 0;width:170px;font-size:14.5px;line-height:22px;color:#444}

/* products band */
.products{position:absolute;left:0;top:1471px;width:777px;height:441px;background:var(--teal);border-radius:0 8px 8px 0}
.products-title{position:absolute;left:110px;top:46px;font-size:40px;font-weight:500;color:var(--white)}
.products-rule{position:absolute;left:111px;top:102px;width:58px;height:3px;background:var(--white)}
.feature{position:absolute;left:111px;width:500px}
.feature .ring{position:absolute;left:0;top:0;width:94px;height:94px;border:3px solid var(--white);border-radius:50%;display:flex;align-items:center;justify-content:center}
.feature h4{position:absolute;left:115px;top:4px;font-size:20px;font-weight:500;color:var(--white);white-space:nowrap}
.feature p{position:absolute;left:117px;top:42px;width:380px;font-size:13.4px;line-height:22px;color:#d8f3ee}
.factory-photo{position:absolute;left:656px;top:1525px;width:432px;height:332px;border-radius:8px;background:linear-gradient(135deg,#9aa3ad 0%,#c9ccd0 45%,#3a3f52 80%,#1e2230 100%)}

/* spotlight */
.shoe-photo{position:absolute;left:161px;top:2045px;width:395px;height:320px;border-radius:45% 40% 35% 40%;background:linear-gradient(150deg,#ff4fa6 0%,#5b5d66 40%,#52d8c9 85%,#eeeeee 100%)}
.hotspot{position:absolute;width:52px;height:52px;border-radius:50%;background:var(--white);border:5px solid #8fe0d6;box-shadow:0 0 0 2px rgba(255,255,255,.6)}
.hotspot::before,.hotspot::after{content:"";position:absolute;left:50%;top:50%;background:#999;transform:translate(-50%,-50%)}
.hotspot::before{width:20px;height:1.5px}
.hotspot::after{width:1.5px;height:20px}
.hotspot.blue{border-color:#2c6ba6}
.tooltip{position:absolute;left:54px;top:2128px;width:163px;height:114px;background:var(--blue);border-radius:8px;color:var(--white);padding:18px 20px}
.tooltip::after{content:"";position:absolute;right:-10px;top:78px;border-left:10px solid var(--blue);border-top:9px solid transparent;border-bottom:9px solid transparent}
.tooltip b{display:block;font-size:18px;font-weight:500}
.tooltip span{display:block;margin-top:10px;font-size:13.5px;line-height:22px}
.spot-title{position:absolute;left:610px;top:2026px;font-size:29px;font-weight:500;color:var(--blue)}
.spot-rule{position:absolute;left:610px;top:2072px;width:52px;height:3px;background:var(--teal)}
.spot-text{position:absolute;left:611px;top:2106px;width:480px;font-size:14.5px;line-height:26px;text-align:justify;color:#444}

/* newsletter */
.newsletter{position:absolute;left:0;top:2432px;width:1200px;height:381px;background:var(--muted-bg)}
.news-title{position:absolute;left:0;top:40px;width:1200px}
.news-rule{position:absolute;left:574px;top:103px}
.news-text{position:absolute;left:0;top:126px;width:1200px;text-align:center;font-size:14.6px}
.email{position:absolute;left:215px;top:183px;width:770px;height:60px;border:1px solid #999;border-radius:30px;background:var(--white);padding:0 26px;display:flex;align-items:center;font-size:16px;color:#333}
.subscribe{position:absolute;left:503px;top:260px;width:195px;height:56px;background:var(--teal)}

/* footer */
.site-footer{position:absolute;left:0;top:2813px;width:1200px;height:371px;background:var(--blue);color:var(--white)}
.foot-brand{position:absolute;left:0;top:50px;width:1200px;display:flex;flex-direction:column;align-items:center;gap:12px}
.foot-brand .brand-dot{background:var(--white);width:52px;height:52px}
.foot-brand .brand-name{color:var(--white);font-size:30px}
.foot-nav{position:absolute;left:0;top:190px;width:1200px;display:flex;justify-content:center;gap:41px;font-size:18px;font-weight:500}
.social{position:absolute;left:514px;top:246px;display:flex;gap:7px}
.social span{width:37px;height:37px;border:2px solid var(--white);border-radius:50%}
.copy{position:absolute;left:0;top:304px;width:1200px;text-align:center;font-size:16px}
</style>
</head>
<body>

<header class="site-header">
  <div class="brand"><span class="brand-dot"></span><span class="brand-name">PACEKITE</span></div>
  <div class="search">Search
    <svg width="14" height="14" viewBox="0 0 14 14"><circle cx="6" cy="6" r="4.3" fill="none" stroke="#333" stroke-width="1.8"/><line x1="9.2" y1="9.2" x2="13" y2="13" stroke="#333" stroke-width="1.8"/></svg>
  </div>
  <nav class="main-nav"><span class="active">Home</span><span>About Us</span><span>Serivces</span><span>Product</span><span>Gallery</span><span>Contact Us</span></nav>
</header>

<section class="hero">
  <div class="hero-photo" role="img" aria-label="Pair of black running shoes with purple and pink soles on a concrete ledge"></div>
  <h1 class="hero-title">PaceKite</h1>
  <p class="hero-text">Sed ut perspiciatis unde omnis iste natus error sit voluptatem accusantium doloremque</p>
  <a class="btn hero-btn">Read More</a>
  <div class="dots"><span></span><span class="on"></span><span></span></div>
</section>

<h2 class="sec-title welcome-title">Welcome to <em>PaceKite</em></h2>
<div class="rule welcome-rule"></div>
<p class="welcome-text">Sed ut perspiciatis unde omnis iste natus error sit voluptatem accusantium doloremque laudantium, totam rem aperiam, eaque ipsa quae ab illo inventore veritatis et quasi architecto beatae vitae dicta sunt explicabo. Nemo enim ipsam voluptatem quia voluptas sit aspernatur aut odit aut fugit, sed quia consequuntur magni dolores eos consequuntur magni qui ratione voluptatem sequi nesciunt.</p>

<div class="cards">
  <div class="card">
    <svg viewBox="0 0 70 84" width="70"><path d="M14 8 L26 12 L35 4 L44 12 L56 8 L54 24 L64 34 L54 44 L56 76 L44 70 L35 80 L26 70 L14 76 L16 44 L6 34 L16 24 Z" fill="none" stroke="#1d6a8e" stroke-width="2.5" stroke-linejoin="round"/></svg>
    <h3>Leather</h3><p>Sed ut perspiciatis unde omnis natus error</p>
  </div>
  <div class="card blue">
    <svg viewBox="0 0 72 84" width="72"><g stroke="#1d6a8e" stroke-width="2" fill="none"><rect x="4" y="8" width="64" height="68"/><path d="M4 25H68M4 42H68M4 59H68M20 8V76M36 8V76M52 8V76" stroke="#1aae9a"/></g></svg>
    <h3>Textile</h3><p>Sed ut perspiciatis unde omnis natus error</p>
  </div>
  <div class="card">
    <svg viewBox="0 0 60 84" width="60"><path d="M30 4 L56 42 L30 80 L4 42 Z" fill="none" stroke="#1d6a8e" stroke-width="2.5" stroke-linejoin="round"/></svg>
    <h3>Synthetic</h3><p>Sed ut perspiciatis unde omnis natus error</p>
  </div>
  <div class="card blue">
    <svg viewBox="0 0 110 84" width="110"><path d="M4 64 L6 52 C30 50 44 40 58 28 L90 32 C100 34 106 44 106 58 L106 64 Z" fill="none" stroke="#1d6a8e" stroke-width="3" stroke-linejoin="round"/><path d="M24 26 L32 34 M32 34 L26 34 M32 34 L32 28" stroke="#1aae9a" stroke-width="2.5" fill="none"/></svg>
    <h3>Upper</h3><p>Sed ut perspiciatis unde omnis natus error</p>
  </div>
</div>

<section class="products">
  <h2 class="products-title">Footwear Products</h2>
  <div class="products-rule"></div>
  <div class="feature" style="top:143px">
    <div class="ring"><svg width="42" height="36" viewBox="0 0 42 36"><g fill="none" stroke="#fff" stroke-width="2"><rect x="3" y="3" width="36" height="24"/><path d="M14 33H28M21 27V33M9 20L33 10"/></g></svg></div>
    <h4>Sed ut perspiciatis unde omnis</h4>
    <p>Nemo enim ipsam voluptatem quia voluptas sit aspernatur aut odit aut fugit, sed quia consequuntur magni dolores eos qui ratione voluptatem sequi nesciunt.</p>
  </div>
  <div class="feature" style="top:292px">
    <div class="ring"><svg width="38" height="38" viewBox="0 0 38 38"><g fill="none" stroke="#fff" stroke-width="2"><rect x="3" y="3" width="32" height="32"/><rect x="9" y="9" width="8" height="20"/><rect x="21" y="9" width="8" height="20"/></g></svg></div>
    <h4>Sed ut perspiciatis unde omnis</h4>
    <p>Nemo enim ipsam voluptatem quia voluptas sit aspernatur aut odit aut fugit, sed quia consequuntur magni dolores eos qui ratione voluptatem sequi nesciunt.</p>
  </div>
</section>
<div class="factory-photo" role="img" aria-label="Shoe factory production line with sneakers on lasts"></div>

<div class="shoe-photo" role="img" aria-label="Pair of grey and pink running shoes with mint soles"></div>
<span class="hotspot" style="left:321px;top:2028px"></span>
<span class="hotspot blue" style="left:230px;top:2207px"></span>
<span class="hotspot" style="left:500px;top:2248px"></span>
<span class="hotspot" style="left:244px;top:2314px"></span>
<div class="tooltip"><b>Welting</b><span>Nemo enim ipsam is voluptatem quia</span></div>

<h2 class="spot-title">Sed ut perspiciatis unde omnis</h2>
<p class="spot-text">Sed ut perspiciatis unde omnis iste natus error sit voluptatem accusantium doloremque laudantium, totam rem aperiam, eaque ipsa quae ab illo inventore veritatis et quasi architecto beatae vitae dicta sunt explicabo. Nemo enim ipsam voluptatem quia voluptas sit aspernatur aut odit aut fugit, sed quia consequuntur magni dolores eos qui ratione voluptatem sequi nesciunt. Neque porro quisquam est, qui dolorem ipsum quia dolor sit amet, consectetur, adipisci velit, sed quia non numquam eius modi tempora incidunt ut labore et dolore magnam aliquam quaerat voluptatem.</p>

<section class="newsletter">
  <h2 class="sec-title news-title">Our <em>Newsletter</em></h2>
  <div class="rule news-rule"></div>
  <p class="news-text">Sed ut perspiciatis unde omnis iste natus error sit voluptatem accusantium doloremque laudantium</p>
  <div class="email">Email :</div>
  <a class="btn subscribe">Subscribe</a>
</section>

<footer class="site-footer">
  <div class="foot-brand"><span class="brand-dot"></span><span class="brand-name">PACEKITE</span></div>
  <nav class="foot-nav"><span>Home</span><span>About Us</span><span>Serivces</span><span>Product</span><span>Gallery</span><span>Contact Us</span></nav>
  <div class="social"><span></span><span></span><span></span><span></span></div>
  <p class="copy">Copyright © 2021. PaceKite All rights reserved.</p>
</footer>

</body>
</html>
```